Black Car Limousine transportation business in Naples Florida

Always stand for my reliability and RVD stands for Love, K and M are the first initials of my children's names. It should show professionalism and a dedication to customer service. We keep our clients identities private. Show our professionalism. We are Black car Black tie company. We service transportation on a reserve basis to and from residents, airports, casinos, hotels,

Target Market(s)

It is a Private car service. High end clients. Businesses, Celebrity and athletes. Service to airports, hotels, special events.

Industry/Entity Type

Business

Contact Information for Business Card

A pearl metallic or Luster card. Standard business card size. Would like the name, Company email, show we take credit cards and phone number. Currently I don't have a website but will like to add later.

Logo Text

STEADFAST RVD TRANSPORTATION

Font styles to use
Serif

Colors
eaeaea
000000

Requirements
Must have
• Must have Company email, show we take credit cards and phone number. Currently I don't have a website but will like to add later.
Nice to have
• Would like to stay with a black and white theme. Open to some color trim.
Should not have
• Open to suggestions

```html
<!DOCTYPE html>
<html lang="en">
<head>
<meta charset="utf-8">
<title>Steadfast RVD Transportation – Business Cards</title>
<link href="https://fonts.googleapis.com/css2?family=Libre+Baskerville:wght@400;700&display=swap" rel="stylesheet">
<style>
  :root{
    --bg:#eaeaea;
    --ink:#000000;
    --front-top:#4b4b4b;
    --front-bottom:#3a3a3a;
    --back:#0d0d0d;
    --wave:#5c5c5c;
    --wave-dark:#2a2a2a;
    --text-light:#f2f2f2;
    --logo:#e2e2e2;
    --vehicle-a:#1a1a1a;
    --vehicle-b:#2f2f2f;
  }
  *{box-sizing:border-box;margin:0;padding:0}
  html,body{width:1200px;height:900px;overflow:hidden}
  body{background:var(--bg);font-family:"Libre Baskerville",Georgia,serif;position:relative}

  .card{position:absolute;width:560px;height:320px;overflow:hidden;
        box-shadow:0 6px 18px rgba(0,0,0,.18)}
  .card--front{left:320px;top:110px;
        background:linear-gradient(var(--front-top) 0 58%, var(--front-bottom) 58% 100%)}
  .card--back{left:320px;top:470px;
        background:radial-gradient(ellipse at 35% 40%, #1e1e1e, var(--back) 70%)}

  .logo{position:absolute;color:var(--logo);font-weight:700;line-height:1}
  .logo__row{display:flex;align-items:flex-end;gap:4px}
  .logo__small{writing-mode:vertical-rl;transform:rotate(180deg);font-size:9px;letter-spacing:1px;padding-bottom:4px}
  .logo__main{font-size:56px;letter-spacing:-1px}
  .logo__sub{display:block;font-size:15px;font-weight:400;letter-spacing:.5px;margin-top:4px}
  .card--front .logo{left:330px;top:52px}
  .card--back .logo{left:340px;top:40px}

  .vehicle{position:absolute;left:110px;top:170px;width:330px;height:125px;border-radius:18px 40px 10px 10px;
           background:linear-gradient(160deg,var(--vehicle-b),var(--vehicle-a) 60%)}

  .contact{position:absolute;left:48px;top:62px;color:var(--text-light)}
  .contact__name{font-size:16px;font-weight:700}
  .contact__role{font-size:12px;margin-top:3px}
  .contact__list{list-style:none;margin-top:14px;font-size:12.5px}
  .contact__list li{display:flex;align-items:center;gap:8px;margin-bottom:5px}
  .contact__list svg{width:13px;height:13px;flex:none}
  .icon-fill{fill:var(--text-light)}
  .contact__address{font-size:12.5px;margin-top:12px;line-height:1.45}

  .wave{position:absolute;left:0;top:0;width:560px;height:320px}
</style>
</head>
<body>

  <section class="card card--front" aria-label="Business card front">
    <div class="logo">
      <div class="logo__row"><span class="logo__small">STEADFAST</span><span class="logo__main">RVD</span></div>
      <span class="logo__sub">TRANSPORTATION</span>
    </div>
    <div class="vehicle" role="img" aria-label="Photo of a black luxury SUV"></div>
  </section>

  <section class="card card--back" aria-label="Business card back">
    <svg class="wave" viewBox="0 0 560 320" aria-hidden="true">
      <path d="M0 320 L0 292 C170 288 360 250 560 160 L560 320 Z" fill="var(--wave)"/>
      <path d="M0 292 C170 288 360 250 560 160" fill="none" stroke="var(--ink)" stroke-width="5"/>
      <path d="M0 320 L0 306 C180 302 330 290 470 226 C380 276 240 308 150 320 Z" fill="var(--wave-dark)"/>
    </svg>

    <div class="logo">
      <div class="logo__row"><span class="logo__small">STEADFAST</span><span class="logo__main">RVD</span></div>
      <span class="logo__sub">TRANSPORTATION</span>
    </div>

    <div class="contact">
      <p class="contact__name">Marcus Bellamy</p>
      <p class="contact__role">Managing Director</p>
      <ul class="contact__list">
        <li><svg viewBox="0 0 24 24" aria-hidden="true"><path class="icon-fill" d="M6.6 10.8a15 15 0 0 0 6.6 6.6l2.2-2.2c.3-.3.7-.4 1-.2 1.1.4 2.3.6 3.6.6.6 0 1 .4 1 1V20c0 .6-.4 1-1 1A17 17 0 0 1 3 4c0-.6.4-1 1-1h3.5c.6 0 1 .4 1 1 0 1.3.2 2.5.6 3.6.1.3 0 .7-.2 1z"/></svg>(239) 555-0147</li>
        <li><svg viewBox="0 0 24 24" aria-hidden="true"><rect class="icon-fill" x="2" y="5" width="20" height="14" rx="1"/><path d="M2 5l10 8 10-8" fill="none" stroke="#0d0d0d" stroke-width="1.8"/></svg>info@rvdtransport.com</li>
        <li><svg viewBox="0 0 24 24" aria-hidden="true"><rect class="icon-fill" x="1" y="4" width="22" height="16" rx="2"/><rect x="1" y="8" width="22" height="3" fill="#0d0d0d"/></svg>All major credit cards accepted</li>
      </ul>
      <p class="contact__address">4410 Harbor Lane,<br>Naples, FL 34102</p>
    </div>
  </section>

</body>
</html>
```